CoinHarbor.com Site Redesign

We are looking to redesign our CoinHarbor.com site. This site is focused on helping consumers make smart financial decisions. We provide reviews and articles in various categories.

We are looking for a responsive design to run on wordpress. We will also have adsense advertisements on our page and will want some ad spot space. We are thinking of two column design vs. single column.

Here is an example of what our competitors look like:
ShopperBeacon.org (mostly reviews vs. articles)
Homepage - https://www.shopperbeacon.example/
Category Review Listing - https://www.shopperbeacon.example/mortgage-refinance/best-mortgage-refinance
Individual Review - https://www.shopperbeacon.example/mortgage-refinance/c/loan-orchard-mortgage-refinance-review

- I like that the site is extremely clean. I like the fixed header in mobile

PilotGuide
Homepage - https://www.pilotguide.example/
Category Review Listing-https://www.pilotguide.example/auto_insurance/index.php
Individual Review- https://www.pilotguide.example/auto_insurance/drivora_review.php

Articles - https://www.pilotguide.example/blog/2017/11/20/going-on-a-holiday-road-trip-be-prepared-for-these-hazards/

What I Like? I like the two column layout in that it gives room for advertising.
What I Do NOT Like? The top navigation is a little cumbersome and old. Mobile view is not very good. Content seems a bit cluttered.

PennyMoth
Homepage - https://www.pennymoth.example
Category Review Listing - https://www.pennymoth.example/blog/insurance/best-car-insurance-companies/?trk=pm_gn1_4.0
Individual Review- https://www.pennymoth.example/blog/insurance/veloro-insurance-review/

What I Like? very clean. Like the use of white space and focus on bright color call to action buttons.
What I Do NOT Like? In mobile a lot of content is pushed below the fold because of the large image above the fold. Reviews are not well organized.

Target Market(s)

consumers interested in saving money and making smart financial decisions

Industry/Entity Type

Financial

Logo Text

CoinHarbor.com or CoinHarbor

Coding

Coded - Design and coding required

Number of Pages Required

5+ page

Font styles to use
Sans Serif

Colors

Designer to choose colors to be used in the design.

Requirements
Must have
• -responsive design
• -room for ad space in the right column
Nice to have
• -good use of white space
• -clean layouts
Should not have
• -clutter

```html
<!DOCTYPE html>
<html lang="en">
<head>
<meta charset="utf-8">
<title>CoinHarbor.com – Make smarter financial decisions</title>
<link href="https://fonts.googleapis.com/css2?family=Open+Sans:wght@400;600;700;800&display=swap" rel="stylesheet">
<style>
:root{
  --brand:#1b5cb8;
  --brand-dark:#14489a;
  --sky:#2a8fd0;
  --nav-bg:#dbe9f7;
  --ink:#111;
  --muted:#444;
  --card-a:#2188c6;
  --card-b:#1656c0;
  --line:#e3e3e3;
}
*{box-sizing:border-box;margin:0;padding:0}
html,body{width:1200px;height:3087px;overflow:hidden;background:#fff}
body{font-family:"Open Sans",Arial,sans-serif;color:var(--ink);position:relative}
.abs{position:absolute}
a{color:inherit;text-decoration:none}

/* header */
.topbar{top:0;left:0;width:1200px;height:64px;background:#fff;border-bottom:1px solid #c9d9ea}
.logo{position:absolute;left:99px;top:16px;display:flex;align-items:center;gap:8px;font-weight:700;font-size:21px;color:var(--brand)}
.logo i{display:block;width:30px;height:30px;background:var(--brand)}
.tagline{position:absolute;left:420px;top:16px;width:362px;height:30px;border-radius:15px;background:var(--sky);color:#fff;font-size:14px;font-weight:600;text-align:center;line-height:30px}
.search{position:absolute;left:945px;top:18px;width:154px;height:28px;display:flex}
.search span{flex:1;border:1px solid #bbb;background:#f4f4f4;font-size:12px;color:#888;line-height:26px;padding-left:8px}
.search b{width:28px;background:var(--brand);display:flex;align-items:center;justify-content:center}
.mainnav{top:64px;left:0;width:1200px;height:58px;background:var(--nav-bg);display:flex;align-items:center}
.mainnav .home{position:absolute;left:99px;top:12px;width:37px;height:34px;background:var(--brand);display:flex;align-items:center;justify-content:center}
.mainnav ul{list-style:none;position:absolute;left:160px;display:flex;gap:30px;font-size:15px;font-weight:600;color:#222}
.mainnav .all{position:absolute;left:969px;font-size:15px;font-weight:600;color:#222}
.mainnav .all:after{content:"";display:inline-block;margin-left:22px;border:5px solid transparent;border-top-color:#888;vertical-align:-2px}

/* hero */
.hero{top:122px;left:0;width:1200px;height:426px;color:#fff;text-align:center;
  background:
    radial-gradient(ellipse 260px 300px at 470px 120px,rgba(150,200,235,.55),transparent 70%),
    radial-gradient(ellipse 300px 340px at 900px 170px,rgba(120,175,220,.5),transparent 70%),
    radial-gradient(ellipse 420px 200px at 130px 380px,rgba(20,70,140,.55),transparent 70%),
    radial-gradient(ellipse 300px 260px at 1120px 60px,rgba(25,80,150,.6),transparent 70%),
    linear-gradient(100deg,#2a6faf 0%,#3d8ecd 40%,#4a97d2 60%,#2a68aa 100%)}
.hero h1{position:absolute;top:158px;width:100%;font-size:32px;font-weight:700;text-shadow:0 1px 4px rgba(0,0,0,.25)}
.hero h2{position:absolute;top:205px;width:100%;font-size:17px;font-weight:700;letter-spacing:.5px}
.hero p{position:absolute;top:237px;width:100%;font-size:16px}
.hero .btn{position:absolute;left:510px;top:281px;width:180px;height:48px;border:2px solid #fff;line-height:44px;font-weight:700;font-size:18px}

/* intro */
.intro{top:570px;left:0;width:1200px;text-align:center}
.intro h2{font-size:27px;font-weight:800}
.intro p{font-size:17px;margin-top:6px}
.feature{top:682px;width:330px;display:flex;gap:14px}
.feature svg{flex:none}
.feature h3{font-size:15px;font-weight:700;margin-top:4px}
.feature p{font-size:13px;color:#222;line-height:1.5;margin-top:6px}
.rule{top:806px;left:99px;width:1002px;height:1px;background:var(--line)}

/* finder */
.finder{top:870px;left:235px;width:730px;height:50px;border:1px solid #999;display:flex}
.finder .lbl{width:259px;background:var(--sky);color:#fff;font-size:22px;font-weight:600;line-height:48px;padding-left:44px}
.finder .sel{flex:1;font-size:20px;font-weight:600;color:#333;line-height:48px;padding-left:24px;position:relative}
.finder .sel:after{content:"";position:absolute;right:28px;top:20px;border:8px solid transparent;border-top-color:#555}

/* category grid */
.tile{width:238px;height:225px;display:flex;align-items:center;justify-content:center;text-align:center;color:#fff;font-weight:700;font-size:21px;text-shadow:0 1px 4px rgba(0,0,0,.6);line-height:1.2}
.t-annu{background:radial-gradient(circle at 40% 35%,#9cc0e2,transparent 55%),radial-gradient(circle at 80% 75%,#c7d3de,transparent 45%),linear-gradient(160deg,#5d93c8,#3a6a9b)}
.t-auto{background:radial-gradient(circle at 55% 40%,#c9a48e,transparent 50%),radial-gradient(circle at 20% 85%,#3c3431,transparent 50%),linear-gradient(160deg,#8d7464,#5a4a42)}
.t-credm{background:radial-gradient(circle at 70% 20%,#b9c67b,transparent 40%),radial-gradient(circle at 45% 70%,#e8e2d6,transparent 50%),linear-gradient(160deg,#8a7a66,#4e443c)}
.t-credr{background:radial-gradient(circle at 35% 45%,#5b5e62,transparent 50%),radial-gradient(circle at 80% 55%,#c0393a,transparent 30%),linear-gradient(160deg,#a5a8ab,#4b4f53)}
.t-debt{background:radial-gradient(circle at 40% 30%,#d9d3c8,transparent 45%),radial-gradient(circle at 65% 80%,#eee,transparent 40%),linear-gradient(160deg,#7f7a73,#3f3d3a)}
.t-idt{background:radial-gradient(circle at 55% 55%,#5d6b78,transparent 55%),linear-gradient(160deg,#38475a,#1c2530)}
.t-life{background:radial-gradient(circle at 50% 40%,#b07f5e,transparent 50%),radial-gradient(circle at 80% 20%,#d0c7be,transparent 35%),linear-gradient(160deg,#6e5343,#3b2d25)}
.t-mort{background:radial-gradient(circle at 55% 55%,#c7a37f,transparent 45%),radial-gradient(circle at 20% 20%,#3b3530,transparent 50%),linear-gradient(160deg,#6b5b4b,#2f2924)}
.t-brok{background:radial-gradient(circle at 45% 35%,#c9c2b8,transparent 45%),linear-gradient(160deg,#7c7e80,#3b3e42)}
.t-pay{background:radial-gradient(circle at 40% 40%,#8b98a5,transparent 50%),linear-gradient(160deg,#4e5965,#262d35)}
.t-pers{background:radial-gradient(circle at 55% 50%,#c59c7d,transparent 50%),radial-gradient(circle at 20% 20%,#e2d8cd,transparent 35%),linear-gradient(160deg,#86705f,#4b3e35)}
.t-stud{background:radial-gradient(circle at 50% 35%,#6f6a63,transparent 50%),radial-gradient(circle at 30% 85%,#364b58,transparent 45%),linear-gradient(160deg,#55575a,#252a2e)}
.t-tax{background:radial-gradient(circle at 70% 40%,#e2e6ea,transparent 45%),radial-gradient(circle at 40% 80%,#6c7f93,transparent 40%),linear-gradient(160deg,#c3ccd4,#8e9aa5)}
.banner{top:1698px;left:354px;width:745px;height:226px;display:flex;align-items:center;justify-content:center;gap:8px;font-weight:700;font-size:21px;color:var(--brand);
  background:radial-gradient(ellipse 160px 120px at 640px 80px,#c6c9cc,transparent 70%),radial-gradient(ellipse 200px 100px at 520px 200px,#b4b9be,transparent 70%),linear-gradient(100deg,#f1f2f3,#dcdfe1)}
.banner i{display:block;width:30px;height:30px;background:var(--brand)}

/* articles */
.sec-title{font-size:29px;font-weight:700}
.card{width:238px;color:#fff;padding:12px 12px 10px}
.card h4{font-size:16px;font-weight:700;line-height:1.3}
.card p{font-size:11.5px;line-height:1.6;margin-top:10px;text-align:justify}
.card a{display:block;font-weight:700;font-size:13px;margin-top:10px}
.c-a{background:var(--card-a)}
.c-b{background:var(--card-b)}
.ad{width:257px;height:207px}
.ad1{top:2019px;left:842px;background:#15152a;color:#fff;padding:12px}
.ad1 .name{font-size:13px;color:#9ad04f}
.ad1 .art{position:absolute;left:12px;top:36px;width:80px;height:155px;background:linear-gradient(#3a3a60,#24244a)}
.ad1 .copy{position:absolute;left:150px;top:70px;width:95px;text-align:center;font-weight:800;font-size:15px;line-height:1.2;color:#fff}
.ad1 .copy em{font-style:normal;color:#f5c400}
.ad1 .go{position:absolute;left:122px;top:168px;width:112px;height:24px;border-radius:12px;background:#1e7fd6;font-size:11px;font-weight:700;text-align:center;line-height:24px}
.ad2{top:2245px;left:842px;height:208px;border:1px solid #ccc;background:#fff;padding:10px 14px}
.ad2 .name{font-size:12px;color:#555;display:flex;align-items:center;gap:6px}
.ad2 .name i{width:12px;height:12px;border-radius:50%;background:#4a86e8;display:block}
.ad2 h5{font-size:19px;font-weight:400;color:#555;line-height:1.3;margin-top:14px;width:190px}
.ad2 .try{position:absolute;left:22px;top:112px;background:#3b78e7;color:#fff;font-size:11px;font-weight:700;padding:6px 10px}
.ad2 .art{position:absolute;right:14px;bottom:14px;width:104px;height:100px;background:linear-gradient(135deg,#f2b233,#e1472f 55%,#3b78e7)}
.ad2 .foot{position:absolute;left:22px;bottom:12px;font-size:12px;color:#666}

/* services */
.svc{list-style:none;font-size:12.5px;line-height:26px}
.svc li{padding-left:16px;position:relative}
.svc li:before{content:"";position:absolute;left:0;top:8px;border:5px solid transparent;border-left:7px solid var(--brand);border-right:0}
.svc .on{color:var(--brand);font-weight:700}
.pop-img{top:2556px;left:687px;width:194px;height:171px;background:radial-gradient(circle at 55% 60%,#fbf8f1,transparent 55%),radial-gradient(circle at 20% 15%,#c0463a,transparent 25%),linear-gradient(150deg,#d9cdb5,#8e7d63)}
.pop{top:2556px;left:895px;width:204px}
.pop h4{font-size:20px;font-weight:700;color:var(--brand);line-height:1.25}
.pop p{font-size:12px;color:#444;line-height:1.55;margin-top:10px;text-align:justify}

/* newsletter */
.news{top:2754px;left:99px;width:1002px;height:203px;background:linear-gradient(90deg,#3fa6dc,#3a7fd6);color:#fff;text-align:center}
.news h3{font-size:29px;font-weight:700;line-height:1.3;margin-top:22px}
.news .field{position:absolute;left:208px;top:125px;width:378px;height:36px;background:#fff;color:#888;font-size:14px;line-height:36px;text-align:left;padding-left:12px}
.news .sub{position:absolute;left:601px;top:125px;width:129px;height:36px;border:2px solid #fff;font-weight:700;font-size:14px;line-height:32px}

.foot-links{top:2988px;left:0;width:1200px;display:flex;justify-content:center;gap:30px;font-size:14px;color:#222}
.copy{top:3032px;left:0;width:1200px;text-align:center;font-size:11.5px;color:#222}
</style>
</head>
<body>

<header class="abs topbar">
  <a class="logo" href="#"><i></i>CoinHarbor.com</a>
  <div class="tagline">Trusted Financial Advice and Reviews Since 2001</div>
  <div class="search"><span>Search</span><b><svg width="13" height="13" viewBox="0 0 13 13"><circle cx="5.5" cy="5.5" r="4" fill="none" stroke="#fff" stroke-width="1.8"/><line x1="8.5" y1="8.5" x2="12" y2="12" stroke="#fff" stroke-width="2"/></svg></b></div>
</header>

<nav class="abs mainnav">
  <a class="home" href="#"><svg width="20" height="18" viewBox="0 0 20 18"><path d="M10 1 1 9h3v8h4v-5h4v5h4V9h3z" fill="#fff"/></svg></a>
  <ul><li>Annuities</li><li>Auto Insurance</li><li>Credit Monitoring</li><li>Debt Management</li><li>Mortgages</li></ul>
  <span class="all">All Categories</span>
</nav>

<section class="abs hero" role="img" aria-label="Smiling couple reviewing finances together, tinted blue">
  <h1>Make smarter financial decisions</h1>
  <h2>FIND THE BEST FINANCIAL PRODUCTS &amp; SERVICES</h2>
  <p>Disclosure: We receive advertising revenue from some partners.</p>
  <a class="btn" href="#">LEARN MORE</a>
</section>

<section class="abs intro">
  <h2>What is CoinHarbor.com?</h2>
  <p>Financial Service Advice and Reviews</p>
</section>

<div class="abs feature" style="left:99px">
  <svg width="76" height="76" viewBox="0 0 76 76"><polygon points="38,4 70,22 70,56 38,74 6,56 6,22" fill="#1d6fc4"/><circle cx="34" cy="36" r="12" fill="#8fd3f5" stroke="#fff" stroke-width="3"/><line x1="43" y1="45" x2="54" y2="56" stroke="#fff" stroke-width="5"/></svg>
  <div><h3>We Analyze &amp; Explain</h3><p>We analyze &amp; explain how each online service works</p></div>
</div>
<div class="abs feature" style="left:434px">
  <svg width="76" height="76" viewBox="0 0 76 76"><polygon points="38,4 70,22 70,56 38,74 6,56 6,22" fill="#1d6fc4"/><rect x="24" y="22" width="8" height="32" fill="#f5b82e"/><rect x="34" y="22" width="8" height="32" fill="#e8532f"/><rect x="44" y="22" width="8" height="32" fill="#f5b82e"/></svg>
  <div><h3>We Test &amp; Compare</h3><p>We test &amp; compare the leading services in each category</p></div>
</div>
<div class="abs feature" style="left:786px">
  <svg width="76" height="76" viewBox="0 0 76 76"><polygon points="38,4 70,22 70,56 38,74 6,56 6,22" fill="#1d6fc4"/><polygon points="38,20 43,33 57,33 46,42 50,56 38,48 26,56 30,42 19,33 33,33" fill="#f5c400"/></svg>
  <div><h3>We Review &amp; Rate</h3><p>We review and rate each service to show which is best</p></div>
</div>
<div class="abs rule"></div>

<div class="abs finder"><div class="lbl">I'm looking for</div><div class="sel">Product or Category</div></div>

<a class="abs tile t-annu"  style="top:973px;left:99px"  role="img" aria-label="Photo of a retired couple smiling">Annuities</a>
<a class="abs tile t-auto"  style="top:973px;left:354px" role="img" aria-label="Photo of hands exchanging car keys">Auto Insurance</a>
<a class="abs tile t-credm" style="top:973px;left:607px" role="img" aria-label="Photo of a credit report on a desk">Credit Monitoring</a>
<a class="abs tile t-credr" style="top:973px;left:860px" role="img" aria-label="Photo of a card payment terminal">Credit Repair</a>
<a class="abs tile t-debt"  style="top:1214px;left:99px" role="img" aria-label="Photo of a desk with calculator and notes">Debt Management</a>
<a class="abs tile t-idt"   style="top:1214px;left:354px" role="img" aria-label="Photo of hands typing on a laptop">Identity Theft</a>
<a class="abs tile t-life"  style="top:1214px;left:607px" role="img" aria-label="Photo of a family relaxing together">Life Insurance</a>
<a class="abs tile t-mort"  style="top:1214px;left:860px" role="img" aria-label="Photo of a small wooden house model">Mortgages</a>
<a class="abs tile t-brok"  style="top:1457px;left:99px" role="img" aria-label="Photo of a man reviewing a tablet">Online Brokerages</a>
<a class="abs tile t-pay"   style="top:1457px;left:354px" role="img" aria-label="Photo of a hand touching a loan screen">Payday Loans</a>
<a class="abs tile t-pers"  style="top:1457px;left:607px" role="img" aria-label="Photo of a child with a piggy bank">Personal Finance</a>
<a class="abs tile t-stud"  style="top:1457px;left:860px" role="img" aria-label="Photo of a student sitting by the water">Student Loan<br>Consolidation</a>
<a class="abs tile t-tax"   style="top:1698px;left:99px" role="img" aria-label="Photo of printed charts and graphs">Tax Settlement</a>
<div class="abs banner" role="img" aria-label="Faded photo of a businessman reading documents"><i></i>CoinHarbor.com</div>

<h2 class="abs sec-title" style="top:1964px;left:97px">Recent Articles</h2>

<article class="abs card c-a" style="top:2019px;left:99px;height:216px"><h4>5 "Easy" Ways Parents Can Save $1000's a Year</h4><p>Parents, let's face it - the high cost of raising children leaves us all needing a little extra money. Short of getting a big raise, switching jobs, or winning....</p><a href="#">Read more</a></article>
<article class="abs card c-b" style="top:2019px;left:346px;height:216px"><h4>Motorcycle Insurance<br>Basics</h4><p>Motorcycle insurance can be quite expensive; it can be the same amount as an auto insurance quote in some cases. Depending on the coverage you select and your driving....</p><a href="#">Read more</a></article>
<article class="abs card c-a" style="top:2019px;left:593px;height:216px"><h4>How Do I Get Cheap Auto Insurance?</h4><p>If you're looking for cheap auto insurance, then you aren't alone. Many drivers regularly search for lower cost, more affordable insurance for their vehicles on a regular basis. If...</p><a href="#">Read more</a></article>
<article class="abs card c-b" style="top:2245px;left:99px;height:208px"><h4>LA Car Insurance Requirements</h4><p>If you live in Louisiana you are no doubt aware that you have to carry LA auto insurance in order to legally operate a motor vehicle. However, just because....</p><a href="#">Read more</a></article>
<article class="abs card c-a" style="top:2245px;left:346px;height:208px"><h4>How Do I Buy General Auto Insurance?</h4><p>Most people already have budgets that are extremely stretched; therefore, it is not surprising that most people want to spend the least amount they possibly can on car insurance....</p><a href="#">Read more</a></article>
<article class="abs card c-b" style="top:2245px;left:593px;height:208px"><h4>How to Shop for Young Driver's Insurance?</h4><p>Everyone one needs car insurance, including young drivers...especially young drivers. Auto insurance for young drivers can often be rather expensive and finding one that fits the needed aspects can...</p><a href="#">Read more</a></article>

<aside class="abs ad ad1">
  <div class="name">pixelforge</div>
  <div class="art" role="img" aria-label="Column of sample logo designs"></div>
  <div class="copy">GET A<br>LOGO<br>DESIGN<br>STARTING<br><em>$99</em></div>
  <div class="go">GET STARTED ›</div>
</aside>
<aside class="abs ad ad2">
  <div class="name"><i></i>Nimbus Cloud</div>
  <h5>Start your first Virtual Machine for free.</h5>
  <div class="try">TRY IT FREE</div>
  <div class="art" role="img" aria-label="Colourful stacked block illustration"></div>
  <div class="foot">Nimbus Cloud</div>
</aside>

<h2 class="abs sec-title" style="top:2490px;left:97px">All Services Reviewed</h2>
<ul class="abs svc" style="top:2548px;left:99px"><li>Annuities</li><li>Auto Insurance</li><li>Credit Monitoring</li><li>Credit Repair</li><li>Debt Management</li><li>Homeowners Insurance</li><li>Identity Theft</li></ul>
<ul class="abs svc" style="top:2548px;left:305px"><li>Life Insurance</li><li>Mortgages</li><li>Online Brokerages</li><li>Payday Loans</li><li>Personal Finance</li><li>Student Loan Consolidation</li><li>Tax Settlement</li></ul>

<h2 class="abs sec-title" style="top:2490px;left:534px">Popular Services Reviewed</h2>
<ul class="abs svc" style="top:2548px;left:539px"><li class="on">Debt Management</li><li>Payday Loans</li><li>Credit Cards</li></ul>
<div class="abs pop-img" role="img" aria-label="Notepad with a debt management plan and pencils"></div>
<div class="abs pop"><h4>Debt Management headlines</h4><p>At vero eos et accusamus et iusto odio dignissimos ducimus qui blanditiis praesentium voluptatum deleniti atque corrupti quos dolores et quas molestias...</p></div>

<section class="abs news">
  <h3>Subscribe to our newsletter to get the latest great deals<br>and reviews</h3>
  <div class="field">Enter Email id</div>
  <div class="sub">SUBSCRIBE</div>
</section>

<nav class="abs foot-links"><a href="#">About us</a><a href="#">Privacy Policy</a><a href="#">Terms of Service</a><a href="#">Contact us</a></nav>
<p class="abs copy">Copyright © 2017 CoinHarbor. All rights reserved.</p>

</body>
</html>
```